Buddhist Center Advertisement

I need a full page single sided 8.5" by 11" flyer for posting around town that describes our upcoming schedule as well as general information about our center. The flyer should be full color and print at 300 DPI. I'm open to a variety of Buddhist imagery, but it should be related to Tibetan Buddhism.
The flyers will be read off bulletin boards so the text shouldn't be too small.
I prefer not to put text over semi-transparent graphics, I think it makes the text too difficult to read.
Target Market(s)
Spiritually minded people seeking instruction in meditation and looking for a new way of relating to themselves and the world, people looking for answers to life's most important questions. The main function of the flyer is to attract new members.
Industry/Entity Type
Town
Requirements
Must have
- 1. our schedule, with class description
Name of Module: "Opening Buddhism: Turning Burdens into Ease"
In this module we will consider well the disadvantages of self-cherishing and the advantages of cherishing others more than ourselves. We will learn how to employ the special techniques of mind training or “lo-jong” as a means to transform problems into happiness, and learn to treat our challenges as precious opportunities for spiritual growth.
Saturday, September 21 10:30 - 12:30
Saturday, September 28 10:30 - 12:30
Saturday, October 26 10:30 - 12:30
Saturday, November 9 10:30 - 6:00 Retreat Day
Saturday, November 23 10:30 - 6:00 Retreat Day
2. Our website, www.vantoraleka.org
3. our phone number (555) 318-2047
4. Our facebook and Gatherly pages
https://www.friendbook.net/VantoralekaCenter
http://www.gatherly.net/vantoraleka-buddhist-center/
5. This text
"The Vantoraleka center is a community of spiritual friends dedicated to the practice of Tibetan Buddhism. We practice in the Gelugpa tradition, the same lineage as his Holiness The Chogye Tulku. The Center was founded in 1994 under the spiritual direction of Lama Tenru Gelwa, and the Society for the Continuance of the Ekayana Path. We offer weekly classes in meditation and Buddhist philosophy suitable for beginners as well as advanced practitioners. All classes are free of charge and offered on a donation basis only.
Nice to have
- our logo

```html
<!DOCTYPE html>
<html lang="en">
<head>
<meta charset="utf-8">
<title>Vantoraleka Center – Opening Buddhism Flyer</title>
<link rel="stylesheet" href="https://fonts.googleapis.com/css2?family=Roboto+Condensed:ital,wght@0,400;0,700;1,700&family=Arimo:ital,wght@0,400;0,700;1,700&family=Tinos:wght@400;700&display=swap">
<style>
  :root {
    --page-bg: #e6e1d9;
    --header-red: #8f1a1f;
    --logo-yellow: #f7ea1c;
    --band-yellow: #f6c500;
    --navy: #272d68;
    --tab-white: #f2f3f7;
    --tab-shade: #c9ccd9;
    --time-yellow: #f7d21a;
    --deep-brown: #17110c;
    --pill-tan: #c2a868;
    --ink: #1d1a14;
    --white: #ffffff;
  }
  * { box-sizing: border-box; margin: 0; padding: 0; }
  html, body { width: 988px; height: 1200px; overflow: hidden; background: var(--page-bg); }

  .flyer {
    position: absolute; left: 30px; top: 0;
    width: 928px; height: 1200px; overflow: hidden;
    background: var(--deep-brown);
    font-family: "Arimo", Arial, sans-serif;
  }

  /* Header */
  .header {
    position: absolute; left: 0; top: 0; width: 928px; height: 624px;
    background: var(--header-red);
  }
  .logo-card {
    position: absolute; left: 47px; top: 32px; width: 266px; height: 271px;
    background: var(--logo-yellow); border-radius: 10px;
    display: flex; flex-direction: column; align-items: center;
  }
  .logo-name {
    margin-top: 92px; display: flex; align-items: center; gap: 10px;
    font-family: "Tinos", "Times New Roman", serif; font-weight: 700;
    font-size: 30px; color: var(--ink);
  }
  .logo-dot { width: 22px; height: 22px; border-radius: 50%; background: var(--header-red); }
  .logo-quote {
    position: absolute; left: 0; right: 0; top: 222px; text-align: center;
    font-family: "Tinos", "Times New Roman", serif; font-size: 17px; color: var(--ink);
  }
  .logo-quote cite {
    display: block; font-style: normal; font-size: 11px;
    text-align: right; padding-right: 26px; margin-top: -1px;
  }

  .module-label {
    position: absolute; left: 368px; top: 62px;
    font-weight: 700; font-size: 17px;
    letter-spacing: 4.5px; color: var(--white);
  }
  .module-title {
    position: absolute; left: 368px; top: 102px; width: 540px;
    font-family: "Roboto Condensed", "Arial Narrow", sans-serif; font-weight: 700;
    font-size: 60px; line-height: 62px; color: var(--white); letter-spacing: -0.5px;
  }
  .module-intro {
    position: absolute; left: 47px; top: 325px; width: 845px;
    font-weight: 700; font-size: 16px; line-height: 24px; color: var(--white);
  }
  .nowrap { white-space: nowrap; }

  /* Schedule */
  .schedule-band {
    position: absolute; left: 29px; top: 441px; width: 869px; height: 41px;
    background: var(--band-yellow); border-radius: 8px 8px 0 0;
    text-align: center; font-size: 24px; line-height: 41px;
    letter-spacing: 5px; color: var(--ink);
  }
  .sessions {
    position: absolute; left: 29px; top: 482px; width: 869px; height: 142px;
    display: flex; gap: 10px;
  }
  .session {
    flex: 1; position: relative; background: var(--navy); text-align: center;
    font-family: "Roboto Condensed", "Arial Narrow", sans-serif; font-weight: 700;
  }
  .session-day {
    position: absolute; left: 6px; right: 6px; top: 4px; height: 30px;
    background: linear-gradient(var(--tab-white) 55%, var(--tab-shade));
    clip-path: polygon(0 0, 100% 0, 91% 100%, 9% 100%);
    font-family: "Arimo", Arial, sans-serif; font-weight: 400;
    font-size: 19px; line-height: 31px; color: var(--navy);
  }
  .session-date { position: absolute; left: 0; right: 0; top: 50px; font-size: 20px; color: var(--white); }
  .session-time { position: absolute; left: 0; right: 0; top: 81px; font-size: 20px; color: var(--time-yellow); }
  .session-note { position: absolute; left: 0; right: 0; top: 112px; font-size: 16px; color: var(--time-yellow); }

  /* About */
  .about-art { position: absolute; left: 0; top: 624px; width: 367px; height: 507px; }
  .about-text {
    position: absolute; left: 415px; top: 662px; width: 450px;
    font-size: 17px; line-height: 28.5px; text-align: justify; color: var(--white);
  }
  .links-pill {
    position: absolute; left: 412px; top: 1020px; width: 461px; height: 34px;
    background: var(--pill-tan); border-radius: 17px;
    text-align: right; padding-right: 16px;
    font-weight: 700; font-style: italic; font-size: 18px; line-height: 34px; color: var(--navy);
  }
  .links {
    position: absolute; right: 67px; top: 1064px; text-align: right;
    font-weight: 700; font-size: 15.5px; line-height: 30px; color: var(--time-yellow);
  }

  /* Footer */
  .footer {
    position: absolute; left: 0; top: 1131px; width: 928px; height: 69px;
    background: var(--band-yellow); color: var(--ink);
  }
  .footer-site {
    position: absolute; left: 31px; top: 0; line-height: 69px;
    font-weight: 700; font-size: 23px;
  }
  .footer-contact {
    position: absolute; left: 334px; top: 0; line-height: 69px;
    font-family: "Roboto Condensed", "Arial Narrow", sans-serif; font-size: 24px;
  }
  .footer-contact strong { font-weight: 700; font-size: 28px; margin-left: 6px; }
  .social-marks { position: absolute; left: 746px; top: 16px; display: flex; gap: 10px; }
  .social-mark { width: 44px; height: 40px; border-radius: 5px; background: var(--navy); }
  .social-mark.alt { width: 58px; background: var(--header-red); }
</style>
</head>
<body>
  <main class="flyer">
    <header class="header">
      <div class="logo-card">
        <div class="logo-name"><span class="logo-dot"></span>Vantoraleka</div>
        <p class="logo-quote">"For Happiness, Cherish Others."<cite>-Lama Tenru Gelwa</cite></p>
      </div>
      <p class="module-label">Name of Module:</p>
      <h1 class="module-title">Opening Buddhism: Turning Burdens into Ease</h1>
      <p class="module-intro">In this module we will consider well the disadvantages of self-cherishing and the advantages of cherishing others more than ourselves. We will learn how to employ the special techniques of mind training or <span class="nowrap">“lo-jong”</span> as a means to transform problems into happiness, and learn to treat our challenges as precious opportunities for spiritual growth.</p>

      <div class="schedule-band">www.vantoraleka.org</div>
      <div class="sessions">
        <div class="session"><div class="session-day">SATURDAY</div><div class="session-date">SEPTEMBER 21</div><div class="session-time">10:30 - 12:30</div></div>
        <div class="session"><div class="session-day">SATURDAY</div><div class="session-date">SEPTEMBER 28</div><div class="session-time">10:30 - 12:30</div></div>
        <div class="session"><div class="session-day">SATURDAY</div><div class="session-date">OCTOBER 26</div><div class="session-time">10:30 - 12:30</div></div>
        <div class="session"><div class="session-day">SATURDAY</div><div class="session-date">NOVEMBER 9</div><div class="session-time">10:30 - 6:00</div><div class="session-note">Retreat Day</div></div>
        <div class="session"><div class="session-day">SATURDAY</div><div class="session-date">NOVEMBER 23</div><div class="session-time">10:30 - 6:00</div><div class="session-note">Retreat Day</div></div>
      </div>
    </header>

    <svg class="about-art" role="img" aria-label="Golden statue of the Buddha, side view of the serene head" viewBox="0 0 367 507" preserveAspectRatio="none">
      <defs>
        <radialGradient id="gold-glow" cx="0.35" cy="0.45" r="0.75">
          <stop offset="0" stop-color="#c9a24a"/>
          <stop offset="0.55" stop-color="#7a5a22"/>
          <stop offset="1" stop-color="#17110c"/>
        </radialGradient>
      </defs>
      <rect width="367" height="507" fill="url(#gold-glow)"/>
    </svg>

    <p class="about-text">The Vantoraleka center is a community of spiritual friends dedicated to the practice of Tibetan Buddhism. We practice in the Gelugpa tradition, the same lineage as his Holiness The Chogye Tulku. The Center was founded in 1994 under the spiritual direction of Lama Tenru Gelwa, and the Society for the Continuance of the Ekayana Path. We offer weekly classes in meditation and Buddhist philosophy suitable for beginners as well as advanced practitioners. All classes are free of charge and offered on a donation basis only.</p>

    <div class="links-pill">Our Friendbook and Gatherly pages</div>
    <p class="links">https://www.friendbook.net/VantoralekaCenter<br>http://www.gatherly.net/vantoraleka-buddhist-center/</p>

    <footer class="footer">
      <span class="footer-site">www.vantoraleka.org</span>
      <span class="footer-contact">CONTACT US: <strong>(555) 318-2047</strong></span>
      <div class="social-marks"><span class="social-mark"></span><span class="social-mark alt"></span></div>
    </footer>
  </main>
</body>
</html>
```